VOMRA Pty Ltd Business Card

Looking for a simple yet eye-catching double-sided business card design using my company logo on one side and contact details on the other.

Target Market(s)

Government

Industry/Entity Type

Communication Systems Engineering

Contact Information for Business Card

VOMRA Pty Ltd

Requirements
Nice to have
• Would be great to have a QR code so details can be scanned into contacts

```html
<!DOCTYPE html>
<html lang="en">
<head>
<meta charset="utf-8">
<title>VOMRA Pty Ltd Business Card</title>
<link href="https://fonts.googleapis.com/css2?family=Open+Sans:wght@400;600;700&display=swap" rel="stylesheet">
<style>
  :root {
    --slate: #343f48;
    --slate-deep: #2b343b;
    --paper: #ffffff;
    --stage: #eceef0;
    --ink-soft: #e9edf0;
  }
  * { margin: 0; padding: 0; box-sizing: border-box; }
  html, body { width: 1200px; height: 780px; overflow: hidden; }
  body {
    background: var(--stage);
    font-family: "Open Sans", Arial, sans-serif;
    position: relative;
  }
  .card {
    position: absolute;
    top: 235px;
    width: 540px;
    height: 310px;
    border-radius: 18px;
    overflow: hidden;
    background: var(--slate);
    box-shadow: 0 6px 18px rgba(0,0,0,0.18);
  }
  .card-front { left: 40px; }
  .card-back { left: 620px; }

  .front-swoop { position: absolute; inset: 0; }

  .brand {
    position: absolute;
    display: flex;
    align-items: center;
    gap: 12px;
    color: var(--paper);
    font-weight: 700;
    letter-spacing: 2px;
  }
  .brand-dot {
    border-radius: 50%;
    background: currentColor;
    flex: none;
  }
  .card-front .brand { left: 30px; top: 24px; font-size: 40px; }
  .card-front .brand-dot { width: 26px; height: 26px; }

  .address {
    position: absolute;
    left: 32px; top: 86px;
    color: var(--paper);
    font-size: 13px;
    line-height: 18px;
  }
  .contact-list {
    position: absolute;
    left: 32px; top: 134px;
    list-style: none;
    color: var(--paper);
    font-size: 13px;
    line-height: 19px;
  }
  .contact-list li { display: flex; align-items: center; gap: 8px; }
  .contact-list svg { width: 12px; height: 12px; flex: none; }

  .person {
    position: absolute;
    right: 30px; top: 150px;
    text-align: right;
    color: var(--paper);
  }
  .person-name { font-size: 28px; font-weight: 700; line-height: 34px; }
  .person-role { font-size: 15px; font-weight: 400; }

  .card-back .brand {
    left: 0; right: 0; top: 0; bottom: 0;
    justify-content: center;
    color: var(--slate-deep);
    font-size: 64px;
    letter-spacing: 4px;
  }
  .card-back .brand-dot { width: 40px; height: 40px; }
</style>
</head>
<body>

  <section class="card card-front" aria-label="Card front with contact details">
    <svg class="front-swoop" viewBox="0 0 540 310" preserveAspectRatio="none" aria-hidden="true">
      <path d="M0,190 C30,250 120,268 250,270 C340,272 390,290 410,310 L0,310 Z" fill="var(--paper)"/>
      <path d="M8,205 C40,250 100,262 170,266" fill="none" stroke="var(--slate)" stroke-width="2"/>
    </svg>

    <div class="brand"><span class="brand-dot"></span>VOMRA</div>

    <p class="address">42-44 Harbour Lane Northgate<br>NSW 2100 Australia</p>

    <ul class="contact-list">
      <li>
        <svg viewBox="0 0 12 12" aria-hidden="true"><path d="M2.5 1 L4.5 1 L5 3.5 L3.8 4.4 C4.4 5.8 5.6 7 7 7.6 L7.9 6.4 L10.5 7 L10.5 9.2 C10.5 10 9.8 10.6 9 10.5 C4.8 10.1 1.6 6.8 1.2 2.6 C1.1 1.7 1.7 1 2.5 1 Z" fill="var(--paper)"/></svg>
        (555) 214-3860
      </li>
      <li>
        <svg viewBox="0 0 12 12" aria-hidden="true"><circle cx="6" cy="6" r="5" fill="none" stroke="var(--paper)" stroke-width="1.2"/><path d="M1 6 H11 M6 1 C3.5 3.5 3.5 8.5 6 11 M6 1 C8.5 3.5 8.5 8.5 6 11" fill="none" stroke="var(--paper)" stroke-width="1"/></svg>
        www.vomra.com.au
      </li>
      <li>
        <svg viewBox="0 0 12 12" aria-hidden="true"><rect x="1" y="2.5" width="10" height="7" rx="1" fill="none" stroke="var(--paper)" stroke-width="1.2"/><path d="M1.5 3 L6 6.5 L10.5 3" fill="none" stroke="var(--paper)" stroke-width="1.1"/></svg>
        admin@vomra.com.au
      </li>
    </ul>

    <div class="person">
      <p class="person-name">Jordan Hale</p>
      <p class="person-role">Co-Founder</p>
    </div>
  </section>

  <section class="card card-back" aria-label="Card back with company name">
    <div class="brand"><span class="brand-dot"></span>VOMRA</div>
  </section>

</body>
</html>
```